Wren Arts Competition Event For Teenagers Needs Promo Graphics

I am in need of graphics for 2019 Prairie Wren Arts Showcase. It is a Wren Arts competition event for teenagers. I need graphics to make an 11x17 poster and a main title graphic that I can use for digital (social, 16x9 for screens, etc). Graphic should include the following 2 logos: the KM Rising Tide logo (this is who we are) and the "circles" logo is the logo of Wren Arts Showcase so that can be incorporated but is not mandatory and does not need to be in color. Tag line for Wren Arts is "Discover. Develop. Deploy." Again, this is optional. Looking for an artistic design - geometric shapes, bright colors, or something along those lines. Something that speaks to teenagers and especially creatives/Wren Arts types. Additionally, Post should include:
Harbor Lane Chapel
March 29-30
(registration & cost info may be added to the poster before design is finalized; still working on those details)

```html
<!DOCTYPE html>
<html lang="en">
<head>
<meta charset="UTF-8">
<title>Prairie Wren Arts Showcase</title>
<link rel="stylesheet" href="https://fonts.googleapis.com/css2?family=Bebas+Neue&family=Montserrat:wght@600;700&display=swap">
<style>
  :root {
    --navy: #2f48a3;
    --sky: #55bfe8;
    --orange: #df6b35;
    --pink: #ecb6b6;
    --gold: #e8c66a;
    --paper: #f8f8f8;
    --white: #ffffff;
  }
  html, body {
    margin: 0;
    padding: 0;
    overflow: hidden;
    background: var(--white);
  }
  .poster {
    position: relative;
    width: 857px;
    height: 1200px;
    overflow: hidden;
    background: var(--paper);
  }
  .poster__shapes {
    position: absolute;
    inset: 0;
  }
  .brand-row {
    position: absolute;
    top: 178px;
    left: 0;
    width: 857px;
    display: flex;
    justify-content: center;
    align-items: center;
    gap: 40px;
  }
  .brand-row__name {
    font-family: "Bebas Neue", sans-serif;
    font-size: 58px;
    line-height: 1;
    color: var(--sky);
    letter-spacing: 1px;
  }
  .brand-row__event {
    display: flex;
    align-items: center;
    gap: 12px;
    font-family: "Bebas Neue", sans-serif;
    font-size: 30px;
    line-height: 1;
    color: var(--orange);
  }
  .brand-row__mark {
    width: 56px;
    height: 56px;
    border-radius: 50%;
    border: 7px solid var(--orange);
    box-sizing: border-box;
  }
  .title {
    position: absolute;
    top: 340px;
    left: 0;
    width: 857px;
    margin: 0;
    text-align: center;
    font-family: "Bebas Neue", sans-serif;
    font-weight: 400;
    font-size: 160px;
    line-height: 152px;
    color: var(--navy);
    letter-spacing: 1px;
  }
  .region {
    position: absolute;
    top: 722px;
    left: 0;
    width: 857px;
    text-align: center;
    font-family: "Bebas Neue", sans-serif;
    font-size: 66px;
    line-height: 1;
    color: var(--sky);
    letter-spacing: 1px;
  }
  .details {
    position: absolute;
    top: 962px;
    left: 166px;
    width: 527px;
    height: 176px;
    border-top: 6px solid var(--white);
    border-bottom: 6px solid var(--white);
    box-sizing: border-box;
    text-align: center;
    color: var(--white);
    font-family: "Montserrat", sans-serif;
  }
  .details__date {
    margin: 18px 0 0;
    font-size: 72px;
    font-weight: 700;
    line-height: 1;
  }
  .details__venue {
    margin: 14px 0 0;
    font-size: 38px;
    font-weight: 600;
    letter-spacing: 3px;
    line-height: 1;
  }
</style>
</head>
<body>
<main class="poster">
  <svg class="poster__shapes" width="857" height="1200" viewBox="0 0 857 1200" aria-hidden="true">
    <polygon class="shape-orange" fill="var(--orange)" points="0,600 120,560 560,700 700,340 857,230 857,1200 0,1200"/>
    <polygon class="shape-navy" fill="var(--navy)" points="0,0 205,0 80,470 0,560"/>
    <polygon class="shape-gold" fill="var(--gold)" points="205,30 330,0 420,0 260,150 215,110"/>
    <polygon class="shape-sky-top" fill="var(--sky)" points="420,0 857,0 857,150 740,260 610,190 470,80"/>
    <ellipse class="shape-circle" fill="var(--paper)" cx="437" cy="545" rx="372" ry="365"/>
    <polygon class="shape-pink" fill="var(--pink)" points="540,935 857,760 857,1200 720,1200"/>
    <polygon class="shape-pink-corner" fill="var(--pink)" points="0,1030 140,1200 0,1200"/>
    <polygon class="shape-sky-right" fill="var(--sky)" points="770,820 857,620 857,1200 760,1200"/>
    <line class="shape-stroke" x1="580" y1="960" x2="660" y2="1200" stroke="var(--gold)" stroke-width="4"/>
    <g class="dots" fill="var(--navy)">
      <circle cx="770" cy="340" r="9"/>
      <circle cx="795" cy="375" r="8"/>
      <circle cx="610" cy="1000" r="9"/>
      <circle cx="650" cy="960" r="8"/>
      <circle cx="690" cy="925" r="9"/>
      <circle cx="735" cy="1020" r="8"/>
      <circle cx="50" cy="1080" r="9"/>
      <circle cx="120" cy="1140" r="9"/>
      <circle cx="80" cy="1175" r="8"/>
      <circle cx="220" cy="55" r="10"/>
      <circle cx="260" cy="70" r="9"/>
    </g>
  </svg>

  <div class="brand-row">
    <span class="brand-row__name">KM Rising Tide</span>
    <span class="brand-row__event"><span class="brand-row__mark"></span>Wren Arts Showcase</span>
  </div>

  <h1 class="title">Wren Arts<br>Showcase</h1>
  <p class="region">Prairie</p>

  <section class="details">
    <p class="details__date">29-30 MART</p>
    <p class="details__venue">Harbor Lane Chapel</p>
  </section>
</main>
</body>
</html>
```